ambitious event and festival agency from austria needs fresh business card design

A new design is due for the new headquarters and the new challenges. We organize events for different target groups from 16 to 60 years. The design should therefore be straightforward and not confused, so we are open to new colors and the logo may also be changed. In general, however, the most interesting suggestions are the most interesting ones. after this order we are looking for more graphics for kalvendra facebook instagramm homepage etc A new design is due for the new headquarters and the new challenges. We organize events for different target groups from 16 to 60 years. The design should therefore be straightforward and not confused, so we are open to new colors and the logo may also be changed. In general, however, the most interesting suggestions are the most interesting ones. after this order we are looking for more graphics for kalvendra facebook instagramm homepage etc A new design is due for the new headquarters and the new challenges. We organize events for different target groups from 16 to 60 years. The design should therefore be straightforward and not confused, so we are open to new colors and the logo may also be changed. In general, however, the most interesting suggestions are the most interesting ones. after this order we are looking for more graphics for kalvendra facebook instagramm homepage etc
Updates

Reason: I am sorry for this decision but i need some more time. No new designs please, there are so many good ones and I will have made a decision in the next 3 days.

Target Market(s)

Industry/Entity Type

Business

Font styles to use
Serif
Sans Serif

Colors

Designer to choose colors to be used in the design.

Requirements
Must have
Nice to have
Should not have

```html
<!DOCTYPE html>
<html lang="en">
<head>
<meta charset="utf-8">
<title>Kalvendra Business Card</title>
<link rel="stylesheet" href="https://fonts.googleapis.com/css2?family=Open+Sans:wght@400;600&display=swap">
<style>
  :root {
    --backdrop: #2b2623;
    --card: #111111;
    --accent: #c8283a;
    --grey: #8b8d8f;
    --light: #e9e9e9;
  }
  * { margin: 0; padding: 0; box-sizing: border-box; }
  html, body { width: 1200px; height: 844px; overflow: hidden; }
  body {
    background: var(--backdrop);
    font-family: "Open Sans", sans-serif;
    position: relative;
  }
  .card {
    position: absolute;
    top: 273px;
    width: 520px;
    height: 297px;
    background: var(--card);
    border-radius: 3px;
    box-shadow: 0 10px 28px rgba(0,0,0,0.45);
  }
  .card--front { left: 60px; }
  .card--back { left: 620px; }

  .brand {
    position: absolute;
    font-weight: 600;
    font-size: 54px;
    letter-spacing: -1px;
    color: var(--grey);
    line-height: 1;
    white-space: nowrap;
  }
  .card--front .brand { left: 40px; top: 62px; }
  .card--back .brand { left: 50%; top: 46%; transform: translate(-50%, -50%); }

  .person {
    position: absolute;
    left: 20px;
    top: 150px;
    width: 220px;
    text-align: right;
    color: var(--light);
  }
  .person__name {
    font-size: 20px;
    font-weight: 600;
    color: var(--grey);
    line-height: 1.2;
  }
  .person__surname { color: var(--accent); }
  .person__role { font-size: 14px; margin-top: 2px; }
  .person__address { font-size: 14px; margin-top: 14px; line-height: 1.3; }

  .contacts {
    position: absolute;
    left: 270px;
    top: 150px;
    list-style: none;
    color: var(--light);
    font-size: 13.5px;
  }
  .contacts li {
    display: flex;
    align-items: center;
    gap: 10px;
    height: 22px;
  }
  .contacts svg { width: 11px; height: 11px; fill: var(--accent); flex: none; }
</style>
</head>
<body>
  <section class="card card--front">
    <div class="brand">kalvendra</div>

    <div class="person">
      <p class="person__name">Daniel <span class="person__surname">Hofer</span></p>
      <p class="person__role">Managing Director</p>
      <p class="person__address">18, Lindengasse Street<br>Vienna, Austria 1070</p>
    </div>

    <ul class="contacts">
      <li>
        <svg viewBox="0 0 12 12" aria-hidden="true"><path d="M2.5 0.8 L4.4 0.5 5.2 3.2 3.9 4.2 C4.6 5.8 6 7.3 7.8 8.1 L8.8 6.8 11.5 7.6 11.2 9.5 C10.9 10.8 9.6 11.4 8.3 11 C4.8 9.9 2.1 7.2 1 3.7 C0.6 2.4 1.2 1.1 2.5 0.8Z"/></svg>
        (043)-512-3368
      </li>
      <li>
        <svg viewBox="0 0 12 12" aria-hidden="true"><path d="M3 0.5 H9 V3.5 H3Z M1 4 H11 V9 H9 V11.5 H3 V9 H1Z M4 8 V10.5 H8 V8Z"/></svg>
        512-336-9021
      </li>
      <li>
        <svg viewBox="0 0 12 12" aria-hidden="true"><path d="M0.5 2 H11.5 V10 H0.5Z M1.3 2.8 L6 6.4 10.7 2.8Z" fill-rule="evenodd"/></svg>
        hello@kalvendra.at
      </li>
      <li>
        <svg viewBox="0 0 12 12" aria-hidden="true"><circle cx="6" cy="6" r="5.5"/></svg>
        www.kalvendra.at
      </li>
    </ul>
  </section>

  <section class="card card--back">
    <div class="brand">kalvendra</div>
  </section>
</body>
</html>
```